Harbor Ledger Funds Bus card and Logo

I need a logo design and Bus card design. The fund focuses on evaluating and investing in minerals (sub-surface rights) and real estate.

Harbor ledger refers to a book of knowledge that each plebe gets when entering the Kelmont Marine Academy (my alma mater)

Target Market(s)

Investors and financial advisors

Contact Information for Business Card

Simple - perhaps a logo with a theme on book of knowledge

Logo Text

Ex Scientia Imperium

Font styles to use
Serif
Sans Serif

Colors

Designer to choose colors to be used in the design.

Requirements
Must have
• memorable logo that is relatively simple

```html
<!DOCTYPE html>
<html lang="en">
<head>
<meta charset="utf-8">
<title>Harbor Ledger Funds – Business Card</title>
<link rel="stylesheet" href="https://fonts.googleapis.com/css2?family=Open+Sans:wght@400;700&family=Questrial&display=swap">
<style>
  :root {
    --backdrop: #5b5b5b;
    --card-light: #f3f3f3;
    --card-dark: #252525;
    --ink: #1f1f1f;
    --ink-soft: #2b2b2b;
    --paper-white: #ffffff;
  }
  * { margin: 0; padding: 0; box-sizing: border-box; }
  html, body { width: 1200px; height: 900px; overflow: hidden; }
  body { background: var(--backdrop); position: relative; font-family: "Open Sans", Arial, sans-serif; }

  .card { position: absolute; top: 200px; width: 310px; height: 502px; }
  .card--front { left: 253px; background: var(--card-light); border-radius: 62px 0 62px 0; color: var(--ink); }
  .card--back { left: 627px; background: var(--card-dark); border-radius: 0 62px 0 62px; }

  .brand-dot { position: absolute; left: 50%; transform: translateX(-50%); border-radius: 50%; }
  .card--front .brand-dot { top: 82px; width: 108px; height: 108px; border: 5px solid var(--ink); }
  .card--back .brand-dot { top: 190px; width: 100px; height: 100px; border: 5px solid var(--paper-white); }

  .brand-name { position: absolute; left: 0; width: 100%; text-align: center;
    font-family: "Questrial", "Century Gothic", sans-serif; font-weight: 400; }
  .card--front .brand-name { top: 219px; font-size: 22px; color: var(--ink); }
  .card--back .brand-name { top: 310px; font-size: 22px; color: var(--paper-white); }

  .holder { position: absolute; left: 32px; top: 300px; }
  .holder__name { font-size: 20px; font-weight: 700; letter-spacing: 0.6px; line-height: 26px; color: var(--ink); }
  .holder__role { font-size: 14.5px; line-height: 18px; color: var(--ink-soft); margin-left: -1px; }

  .contact-list { list-style: none; margin-top: 6px; font-size: 14.5px; line-height: 18.5px; color: var(--ink-soft); }
  .contact-list li { display: flex; align-items: center; }
  .contact-list svg { width: 11px; height: 11px; margin-right: 4px; fill: var(--ink); flex: none; }

  .address { margin-top: 6px; font-size: 14.5px; line-height: 18.5px; color: var(--ink-soft); }
</style>
</head>
<body>
  <section class="card card--front" aria-label="Business card front">
    <span class="brand-dot" aria-hidden="true"></span>
    <p class="brand-name">Harbor Ledger Funds</p>

    <div class="holder">
      <h1 class="holder__name">DANIEL MARLOW</h1>
      <p class="holder__role">Managing Director</p>
      <ul class="contact-list">
        <li><svg viewBox="0 0 12 12" aria-hidden="true"><path d="M1 4c0-2 2-3 5-3s5 1 5 3v1H8.5V3.8h-5V5H1z M3 5.5h6l1.5 5.5h-9z"/></svg>044-123 456 789</li>
        <li><svg viewBox="0 0 12 12" aria-hidden="true"><path d="M3.5 0h5a1 1 0 0 1 1 1v10a1 1 0 0 1-1 1h-5a1 1 0 0 1-1-1V1a1 1 0 0 1 1-1zm.5 1.5v7.5h4V1.5zM6 9.8a.7.7 0 1 0 0 1.4.7.7 0 0 0 0-1.4z"/></svg>044-123 456 789</li>
        <li><svg viewBox="0 0 12 12" aria-hidden="true"><path d="M0.5 2.5h11v7h-11z M1 3l5 3.5L11 3" fill="var(--ink)"/><path d="M1.2 3.2 6 6.6l4.8-3.4" fill="none" stroke="var(--card-light)" stroke-width="0.9"/></svg>info@webname.com</li>
        <li><svg viewBox="0 0 12 12" aria-hidden="true"><circle cx="6" cy="6" r="5.5"/><path d="M3 4.5c1 .3 1.5 1 1.2 2 .8.3 1.3 1.3 1 2.4M7.5 2c-.5 1 .5 1.8 1.8 1.8M8 7.5c.6-.3 1.5 0 2 .8" fill="none" stroke="var(--card-light)" stroke-width="0.9"/></svg>www.websitename.com</li>
      </ul>
      <p class="address">12345, Address Goes Here<br>Country Name, 123456.</p>
    </div>
  </section>

  <section class="card card--back" aria-label="Business card back">
    <span class="brand-dot" aria-hidden="true"></span>
    <p class="brand-name">Harbor Ledger Funds</p>
  </section>
</body>
</html>
```